Fotógrafo necesita portada completa para un libro de negocios enfocado a fotografía

Necesito la portada, contraportada y lomo de un libro de tapa blanda que venderé en Valdoria llamado “Las claves para prosperar con la cámara”. Adjunto medidas requeridas por Valdoria.

“Las claves para prosperar con la cámara” es un libro de negocios orientado a fotógrafos, no un libro de fotografía en sí mismo. Detallo las necesidades a continuación:

- Descripción general: Necesito que el diseño sea llamativo, pero lo suficientemente sencillo, moderno y atractivo como para que el cliente perciba en el diseño que el interior contiene un gran valor. No quiero elementos recargados ni diseños muy complicados de entender. Para más inspiración, ver las portadas de libros como "Las mañas del pudiente", "La mente del caudal", "rutinas cuánticas", siguiendo el estilo de mi marca personal: www.ruperlosada.net
- Portada: La portada debe expresar sensaciones de emoción y libertad (al emprender un negocio fotográfico de la forma que transmito en el interior del libro), pero también de misterio (debido a esos “secretos” para vivir del negocio de la fotografía)
- Contraportada: dividida en dos secciones: Una para la breve descripción del libro y otra para la descripción de la biografía del autor con foto.

Por último, necesito el diseño editable en .PSD con los textos provisionales “lorem ipsum”, ya que todavía no tengo los textos definitivos y seré yo quien los integre, así que aprovecharé esos campos de texto, con la fuente, tamaño y color para hacerlo.

Target Market(s)

Photographers

Industry/Entity Type

Photography, economy, marketing

Font styles to use
Serif
Sans Serif

Requirements
Must have
• Title: Las claves para prosperar con la cámara (Capital or not. Depending on design), Subtitle: El manual completo para ejercer con la cámara sin rendirse por el camino. Author: Ruperto Losada
Should not have
• pictures, photos, ¿gradients?

```html
<!DOCTYPE html>
<html lang="es">
<head>
<meta charset="utf-8">
<title>Las claves para prosperar con la cámara — cubierta completa</title>
<link href="https://fonts.googleapis.com/css2?family=Anton&family=Cinzel:wght@400;600;700&family=Open+Sans:wght@600;700&family=Oswald:wght@500;700&display=swap" rel="stylesheet">
<style>
  :root{
    --tan:#9b856b;
    --tan-light:#b49c80;
    --glow:#c3ae94;
    --brown-dark:#5a2f24;
    --brown:#7a4236;
    --coral:#c9705a;
    --coral-bright:#d4684e;
    --blush:#efc5b4;
    --blush-pale:#f6dccf;
    --silver:#ece8e6;
    --white:#ffffff;
  }
  *{margin:0;padding:0;box-sizing:border-box}
  html,body{width:1200px;height:873px;overflow:hidden;background:var(--tan)}
  .cover{position:relative;width:1200px;height:873px;background:var(--tan);overflow:hidden}

  /* ---------- back cover ---------- */
  .back__glow{position:absolute;left:10px;top:70px;width:570px;height:240px;
    background:radial-gradient(ellipse at 45% 45%,var(--glow) 0%,rgba(195,174,148,0.55) 45%,rgba(155,133,107,0) 75%)}
  .back__blurb{position:absolute;left:37px;top:94px;width:512px;
    font:700 15.6px/20.2px "Open Sans",sans-serif;color:var(--white)}
  .back__blurb p + p{margin-top:20px}
  .back__author{position:absolute;right:655px;top:498px;
    font:400 34px/1 "Cinzel",serif;color:var(--silver);letter-spacing:0.5px}
  .back__bio{position:absolute;left:38px;top:532px;width:320px;text-align:right;
    font:600 16.5px/22px "Cinzel",serif;color:var(--brown);letter-spacing:1.2px;
    -webkit-text-stroke:0.4px var(--blush);}
  .back__bio .last{font-size:15px;letter-spacing:0.4px}
  .back__photo{position:absolute;left:367px;top:536px;width:181px;height:181px;
    background:var(--white);border:1px solid #6b6b6b}

  /* ---------- spine ---------- */
  .spine{position:absolute;left:576px;top:0;width:46px;height:873px}
  .spine__title{position:absolute;left:8px;top:28px;writing-mode:vertical-rl;
    font:700 27px/30px "Oswald",sans-serif;color:var(--blush);white-space:nowrap;letter-spacing:-0.5px}
  .spine__title .big{font-family:"Anton",sans-serif;font-weight:400;color:var(--coral);font-size:30px}
  .spine__title .accent{font-family:"Anton",sans-serif;font-weight:400;color:var(--brown);font-size:30px;letter-spacing:1px}
  .spine__title .accent-light{font-family:"Anton",sans-serif;font-weight:400;color:var(--blush-pale);font-size:30px;letter-spacing:1px}
  .spine__author{position:absolute;left:10px;top:616px;writing-mode:vertical-rl;
    font:400 19px/26px "Cinzel",serif;color:var(--silver);white-space:nowrap}
  .spine__image{position:absolute;left:0;top:778px;width:42px;height:90px;
    background:linear-gradient(180deg,#8d8d8d,#5e5e5e 55%,#a9a9a9)}

  /* ---------- front cover ---------- */
  .front__tag{position:absolute;left:688px;top:33px;width:432px;text-align:center;
    font:700 23px/1 "Open Sans",sans-serif;color:var(--brown-dark);letter-spacing:0.4px;white-space:nowrap}
  .front__los{position:absolute;left:668px;top:110px;width:96px;transform:rotate(-90deg);
    font:400 62px/1 "Anton",sans-serif;color:var(--blush);text-align:center;
    -webkit-text-stroke:1.5px var(--coral)}
  .front__key{position:absolute;left:748px;top:62px;width:374px;text-align:right;
    font:400 118px/1.15 "Anton",sans-serif;color:var(--coral);letter-spacing:-1px;white-space:nowrap}
  .front__lead{position:absolute;left:690px;top:178px;width:430px;text-align:right;
    font:italic 700 38px/1 "Oswald",sans-serif;color:var(--blush);white-space:nowrap;
    transform:skewX(-8deg);transform-origin:right}
  .front__word{position:absolute;font-family:"Anton",sans-serif;font-weight:400;
    transform:rotate(-10deg);transform-origin:left bottom;white-space:nowrap;
    -webkit-background-clip:text;background-clip:text;color:transparent}
  .front__word--top{left:652px;top:208px;font-size:124px;line-height:1;
    background-image:linear-gradient(180deg,#9b5a4c,#5e2c22);
    filter:drop-shadow(2px 3px 2px rgba(60,30,20,0.45))}
  .front__word--bottom{left:690px;top:318px;font-size:112px;line-height:1;
    background-image:linear-gradient(180deg,#f7dfd4 0%,#e9bfae 55%,#8a6a5c 100%);
    filter:drop-shadow(2px 3px 2px rgba(60,30,20,0.35))}
  .front__art{position:absolute;left:857px;top:278px;width:296px;height:296px;border-radius:14px;
    background:radial-gradient(ellipse at 60% 55%,#c88a6e 0%,#b4745a 35%,rgba(155,133,107,0) 72%)}
  .front__photo{position:absolute;left:635px;top:574px;width:430px;height:299px;
    background:linear-gradient(200deg,rgba(155,133,107,0) 0%,#8a8078 28%,#57524e 60%,#6f6a66 100%)}
  .front__subtitle{position:absolute;left:712px;top:722px;width:406px;text-align:center;
    font:700 21px/1 "Open Sans",sans-serif;color:var(--coral-bright);white-space:nowrap}
  .front__author{position:absolute;left:694px;top:770px;width:416px;text-align:center;
    font:400 48px/1 "Cinzel",serif;color:var(--silver);white-space:nowrap}
</style>
</head>
<body>
<div class="cover">

  <section class="back">
    <div class="back__glow"></div>
    <div class="back__blurb">
      <p>Brief Description here. Brief Description here. Brief Description here. Brief Description here. Brief Description here. Brief Description here. Brief Description here. Brief Description here. Brief Description here. Brief Description here. Brief Description here. Brief Description here. Brief Description here. Brief Description here. Brief Description here.</p>
      <p>Brief Description here. Brief Description here. Brief Description here. Brief Description here. Brief Description here. Brief Description here. Brief Description here. Brief Description here.</p>
    </div>
    <div class="back__author">AUTHOR’S NAME</div>
    <div class="back__bio">
      About the author About the author<br>
      About the author About the author<br>
      About the author About the author<br>
      About the author About the author<br>
      <span class="last">About the author About the author</span>
    </div>
    <div class="back__photo" role="img" aria-label="Espacio para la foto del autor"></div>
  </section>

  <section class="spine">
    <div class="spine__title">LAS <span class="big">Claves</span> para prosperar con la <span class="accent">CÁ</span><span class="accent-light">MARA</span></div>
    <div class="spine__author">AUTHOR’S NAME</div>
    <div class="spine__image" role="img" aria-label="Pequeña foto de manos sujetando una cámara réflex"></div>
  </section>

  <section class="front">
    <div class="front__tag">OVER THREE&nbsp; MILLION COPIES SOLD</div>
    <div class="front__los">LAS</div>
    <div class="front__key">Claves</div>
    <div class="front__lead">para prosperar con la</div>
    <div class="front__art" role="img" aria-label="Ilustración en acuarela de dos cámaras retro con correa de cuero"></div>
    <div class="front__word front__word--top">CÁ</div>
    <div class="front__word front__word--bottom">MARA</div>
    <div class="front__photo" role="img" aria-label="Foto en tonos sepia de manos con guante sujetando una cámara réflex"></div>
    <div class="front__subtitle">SUBTITLE HERE SUBTITLE HERE“““</div>
    <div class="front__author">AUTHOR’S NAME</div>
  </section>

</div>
</body>
</html>
```